Business Card Design Project

Business card based on attached logo

Todd Merrick
Todd@lorvantest.com
877-514-9073 ext. 318
Www.LorvanTest.com

Industry/Entity Type

Business

```html
<!DOCTYPE html>
<html lang="en">
<head>
<meta charset="utf-8">
<title>LorvanTest Business Cards</title>
<link rel="stylesheet" href="https://fonts.googleapis.com/css2?family=Roboto:wght@400;900&display=swap">
<style>
  :root {
    --stage: #8a8c8f;
    --red: #e31e24;
    --red-deep: #b91c22;
    --ink: #1f1c1d;
    --white: #ffffff;
    --charcoal-light: #4a4a4a;
    --charcoal-dark: #1c1c1c;
    --card-radius: 24px;
  }
  html, body {
    margin: 0;
    padding: 0;
    width: 1200px;
    height: 720px;
    overflow: hidden;
    background: var(--stage);
    font-family: "Roboto", Arial, sans-serif;
  }
  .sheet { position: relative; width: 1200px; height: 720px; }
  .card {
    position: absolute;
    width: 564px;
    height: 322px;
    border-radius: var(--card-radius);
    overflow: hidden;
    box-sizing: border-box;
  }
  .card--contact { left: 34px; top: 26px; background: var(--white); border: 1px solid #555; }
  .card--white { left: 615px; top: 26px; background: var(--white); border: 1px solid #555; }
  .card--dark {
    left: 32px; top: 372px;
    background: radial-gradient(ellipse at 50% 35%, var(--charcoal-light), var(--charcoal-dark) 75%);
  }
  .card--red {
    left: 615px; top: 372px;
    background: linear-gradient(135deg, var(--red) 0%, var(--red-deep) 100%);
  }
  .band { position: absolute; inset: 0; }
  .holder-name {
    position: absolute; right: 44px; top: 28px;
    color: var(--white); font-size: 19px; font-weight: 400; letter-spacing: 0.3px;
    text-transform: uppercase;
  }
  .brand {
    position: absolute;
    display: flex; align-items: center; gap: 12px;
  }
  .brand__name {
    font-weight: 900; letter-spacing: -1px; line-height: 1;
  }
  .brand__mark { width: 22px; height: 22px; background: var(--red); }
  .card--contact .brand { left: 62px; top: 128px; }
  .card--contact .brand__name { font-size: 56px; color: var(--ink); }
  .card--white .brand { left: 0; right: 0; top: 100px; justify-content: center; }
  .card--white .brand__name { font-size: 78px; color: var(--ink); }
  .card--white .brand__mark { width: 28px; height: 28px; }
  .card--dark .brand { left: 0; right: 0; top: 112px; justify-content: center; }
  .card--dark .brand__name { font-size: 78px; color: var(--white); }
  .card--dark .brand__mark { width: 28px; height: 28px; }
  .card--red .brand { left: 36px; top: 52px; }
  .card--red .brand__name { font-size: 78px; color: var(--white); }
  .card--red .brand__mark { width: 28px; height: 28px; background: var(--white); }
  .contact-list {
    position: absolute; left: 70px; top: 238px;
    margin: 0; padding: 0; list-style: none;
    font-size: 17px; color: var(--ink);
  }
  .contact-list li { display: flex; align-items: center; gap: 8px; height: 25px; }
  .contact-list svg { width: 13px; height: 13px; flex: none; }
  .web {
    position: absolute; font-size: 16px; letter-spacing: 2.6px;
  }
  .card--white .web { left: 0; right: 0; bottom: 22px; text-align: center; color: var(--ink); }
  .card--dark .web { left: 0; right: 0; bottom: 28px; text-align: center; color: var(--white); }
  .card--red .web { left: 36px; bottom: 20px; color: var(--white); }
  .faint-square { position: absolute; }
  .card--contact .faint-square { right: -12px; bottom: -12px; width: 104px; height: 104px; background: rgba(227, 30, 36, 0.08); }
  .card--red .faint-square { right: -20px; bottom: -20px; width: 150px; height: 150px; background: rgba(255, 255, 255, 0.12); }
</style>
</head>
<body>
<main class="sheet">

  <section class="card card--contact">
    <svg class="band" viewBox="0 0 564 322" preserveAspectRatio="none" aria-hidden="true">
      <defs>
        <linearGradient id="bandRed" x1="0" y1="0" x2="1" y2="0">
          <stop offset="0" stop-color="#e31e24"/>
          <stop offset="1" stop-color="#b91c22"/>
        </linearGradient>
      </defs>
      <path d="M0 0 H564 V150 C470 95 300 45 0 62 Z" fill="url(#bandRed)"/>
      <path d="M0 62 C300 45 470 95 564 150 V172 C460 100 290 60 0 80 Z" fill="#1f1c1d"/>
      <path d="M0 80 C290 60 460 100 564 172 V176 C455 108 285 68 0 86 Z" fill="#ffffff"/>
    </svg>
    <div class="holder-name">Todd Merrick</div>
    <div class="brand"><span class="brand__name">LorvanTest</span><span class="brand__mark"></span></div>
    <ul class="contact-list">
      <li>
        <svg viewBox="0 0 16 16" aria-hidden="true"><circle cx="8" cy="8" r="7" fill="none" stroke="#e31e24" stroke-width="1.6"/><path d="M5.5 4.5 L7 6.5 L6.2 7.4 C6.8 8.6 7.4 9.2 8.6 9.8 L9.5 9 L11.5 10.5 L10.6 11.8 C7.6 11.4 4.6 8.4 4.2 5.4 Z" fill="#e31e24"/></svg>
        877-514-9073 ext. 318
      </li>
      <li>
        <svg viewBox="0 0 16 16" aria-hidden="true"><rect x="1" y="3.5" width="14" height="10" rx="1.5" fill="#e31e24"/><path d="M1.8 4.5 L8 9 L14.2 4.5" fill="none" stroke="#fff" stroke-width="1.3"/></svg>
        Todd@lorvantest.com
      </li>
      <li>
        <svg viewBox="0 0 16 16" aria-hidden="true"><circle cx="8" cy="8" r="6.5" fill="none" stroke="#e31e24" stroke-width="1.4"/><ellipse cx="8" cy="8" rx="2.8" ry="6.5" fill="none" stroke="#e31e24" stroke-width="1.2"/><path d="M1.5 8 H14.5" stroke="#e31e24" stroke-width="1.2"/></svg>
        www.lorvantest.com
      </li>
    </ul>
    <div class="faint-square"></div>
  </section>

  <section class="card card--white">
    <div class="brand"><span class="brand__name">LorvanTest</span><span class="brand__mark"></span></div>
    <div class="web">www.lorvantest.com</div>
  </section>

  <section class="card card--dark">
    <div class="brand"><span class="brand__name">LorvanTest</span><span class="brand__mark"></span></div>
    <div class="web">www.lorvantest.com</div>
  </section>

  <section class="card card--red">
    <div class="brand"><span class="brand__name">LorvanTest</span><span class="brand__mark"></span></div>
    <div class="faint-square"></div>
    <div class="web">www.lorvantest.com</div>
  </section>

</main>
</body>
</html>
```